Vantoq Business Card Project showing the logo and a marbo image on the rear

Design a whacky but professional business card, the logo is for the front and the Marbo image is for the rear. Happy to consider other open source Marbo Images if the designer wants to select one from the web. Vantoq is a competitor to OMB.com.au and Pellory.com.au and is based around every property in Australia

Target Market(s)

Business

Contact Information for Business Card

Name, Title, Email, Web, Phone Number

Font styles to use
Other font styles liked:
• avenir

Requirements
Must have
• Image on Back logo on front
Nice to have
• Happy to consider other images on rear, preftably Colin Marbo. Image supplied I own, we can use open source other Marbo Images

```html
<!DOCTYPE html>
<html lang="en">
<head>
<meta charset="utf-8">
<title>Vantoq Business Card</title>
<link href="https://fonts.googleapis.com/css2?family=Montserrat:wght@400;500;600;800&display=swap" rel="stylesheet">
<style>
  :root {
    --backdrop: #2b2b2b;
    --card: #1c1c1c;
    --card-soft: #262626;
    --orange: #f28c1f;
    --white: #ffffff;
    --ink: #1c1c1c;
  }
  * { margin: 0; padding: 0; box-sizing: border-box; }
  html, body {
    width: 1200px; height: 900px; overflow: hidden;
    background: var(--backdrop);
    font-family: "Montserrat", sans-serif;
  }
  .canvas { position: relative; width: 1200px; height: 900px; }
  .card {
    position: absolute; left: 240px;
    width: 720px; height: 400px;
    background: var(--card);
    border-radius: 4px;
    overflow: hidden;
    box-shadow: 0 14px 30px rgba(0,0,0,.45);
  }
  .card--front { top: 40px; }
  .card--back { top: 460px; }

  .brand {
    position: absolute;
    display: flex; align-items: center; gap: 16px;
    color: var(--white);
    font-weight: 800;
    letter-spacing: 1px;
    white-space: nowrap;
  }
  .brand__mark { flex: none; background: var(--orange); border-radius: 3px; }

  .card--front .brand { left: 380px; top: 70px; font-size: 66px; }
  .card--front .brand__mark { width: 48px; height: 48px; }

  .info-band { position: absolute; left: 0; top: 190px; width: 720px; height: 170px; }
  .holder { position: absolute; left: 36px; top: 222px; color: var(--white); }
  .holder__name { font-size: 22px; font-weight: 600; letter-spacing: 1.5px; }
  .holder__title { font-size: 17px; font-weight: 400; margin-top: 4px; }

  .contact {
    position: absolute; left: 300px; top: 252px;
    list-style: none; color: var(--white);
    font-size: 17px; font-weight: 400; line-height: 1.55;
  }
  .contact li { display: flex; align-items: center; gap: 8px; }
  .contact svg { width: 14px; height: 14px; flex: none; }

  .card--front .band-brand {
    left: 540px; top: 270px;
    font-size: 34px; gap: 10px; color: var(--ink);
  }
  .band-brand .brand__mark { width: 26px; height: 26px; background: var(--ink); }

  .rear-image {
    position: absolute; right: 0; top: 0;
    width: 400px; height: 400px;
    background: linear-gradient(135deg, var(--card-soft) 0%, #202020 55%, var(--card) 100%);
  }
  .card--back .brand { left: 70px; top: 150px; font-size: 88px; }
  .card--back .brand__mark { width: 64px; height: 64px; }
</style>
</head>
<body>
<main class="canvas">

  <section class="card card--front" aria-label="Card front">
    <div class="brand"><span class="brand__mark"></span>Vantoq</div>

    <svg class="info-band" viewBox="0 0 720 170" aria-hidden="true">
      <polygon fill="var(--orange)" points="0,10 120,10 132,0 720,0 720,170 0,170"/>
    </svg>

    <div class="holder">
      <p class="holder__name">DARREN HOLT</p>
      <p class="holder__title">Director</p>
    </div>

    <ul class="contact">
      <li>
        <svg viewBox="0 0 16 16" aria-hidden="true"><path fill="var(--white)" d="M4 1l3 3-2 2c1 2 3 4 5 5l2-2 3 3-2 2C7 14 2 9 2 3z"/></svg>
        555-214-0391
      </li>
      <li>
        <svg viewBox="0 0 16 16" aria-hidden="true"><rect x="1.5" y="3.5" width="13" height="9" fill="none" stroke="var(--white)" stroke-width="1.4"/><path d="M1.5 3.5l6.5 5 6.5-5" fill="none" stroke="var(--white)" stroke-width="1.4"/></svg>
        info@vantoq.com.au
      </li>
      <li>
        <svg viewBox="0 0 16 16" aria-hidden="true"><g fill="none" stroke="var(--white)" stroke-width="1.2"><circle cx="8" cy="8" r="6.5"/><ellipse cx="8" cy="8" rx="3" ry="6.5"/><path d="M1.5 8h13M3 4.5h10M3 11.5h10"/></g></svg>
        www.vantoq.com.au
      </li>
    </ul>

    <div class="brand band-brand"><span class="brand__mark"></span>Vantoq</div>
  </section>

  <section class="card card--back" aria-label="Card back">
    <div class="rear-image" role="img" aria-label="Faint large property image on the rear of the card"></div>
    <div class="brand"><span class="brand__mark"></span>Vantoq</div>
  </section>

</main>
</body>
</html>
```